Halvorsen Construction Needs a Business Card

Our current business card is very bland, and since we have a new logo, we would like a new business card design to reflect our company. It can be a single-sided or two-sided card, but it is important that our contact information appears on the same side. I am attaching a copy of our old card and our new logo. If you need the logo in another format than the one I'm sending, please let me know. This is the information that we must have on our card, but not necessarily in any specific order:
1) Our logo
2) General Contractor
3) Derek Halvorsen, Owner
4) 482 Commerce Ridge Road, Millbrook Falls, Alabama 35999
5) Office: 256-384-7150
7) Fax: 256-384-7151
8) Cell: 256-619-7150
9) halvorsenconstruction@qrm.net
10) halvorsenconstruction.com (can be omitted if necessary)
Also, I will need files in a format that I can alter if any of the above information changes in the near future. Thank you in advance for your submissions!
Target Market(s)
Commercial and residential clients, architects, and subcontractors.
Industry/Entity Type
Business

```html
<!DOCTYPE html>
<html lang="en">
<head>
<meta charset="utf-8">
<title>Halvorsen Construction – Business Card</title>
<link href="https://fonts.googleapis.com/css2?family=Tinos:wght@400;700&display=swap" rel="stylesheet">
<style>
  :root {
    --backdrop: #5ecfbd;
    --card-grey: #4a4949;
    --card-blue: #1b4fd8;
    --ink: #121212;
    --shadow: rgba(0, 0, 0, 0.22);
  }
  html, body {
    margin: 0;
    padding: 0;
    width: 1200px;
    height: 900px;
    overflow: hidden;
    background: var(--backdrop);
  }
  .canvas {
    position: relative;
    width: 1200px;
    height: 900px;
    display: flex;
    align-items: center;
    justify-content: center;
  }
  .business-card {
    position: relative;
    width: 840px;
    height: 480px;
    overflow: hidden;
    box-shadow: 0 18px 40px var(--shadow);
    font-family: "Tinos", "Times New Roman", serif;
    color: var(--ink);
  }
  .card-bg {
    position: absolute;
    inset: 0;
    width: 100%;
    height: 100%;
  }
  .brand {
    position: absolute;
    top: 56px;
    left: 56px;
    right: 56px;
    display: flex;
    align-items: center;
    gap: 18px;
  }
  .brand-square {
    flex: none;
    width: 64px;
    height: 64px;
    background: var(--ink);
  }
  .brand-name {
    font-weight: 700;
    font-size: 38px;
    line-height: 1;
    letter-spacing: 1px;
    text-transform: uppercase;
    white-space: nowrap;
  }
  .contact {
    position: absolute;
    left: 56px;
    bottom: 48px;
    font-size: 19px;
    line-height: 1.38;
  }
  .contact-gap {
    height: 10px;
  }
</style>
</head>
<body>
<main class="canvas">
  <article class="business-card">
    <svg class="card-bg" viewBox="0 0 840 480" preserveAspectRatio="none" aria-hidden="true">
      <rect x="0" y="0" width="840" height="480" fill="var(--card-blue)"/>
      <polygon points="0,0 560,0 300,480 0,480" fill="var(--card-grey)"/>
    </svg>

    <header class="brand">
      <div class="brand-square"></div>
      <div class="brand-name">Halvorsen Construction</div>
    </header>

    <section class="contact">
      <div>Derek Halvorsen, Owner</div>
      <div>General Contractor</div>
      <div>482 Commerce Ridge Road, Millbrook Falls, Alabama 35999</div>
      <div>Office: 256-384-7150</div>
      <div>Fax: 256-384-7151</div>
      <div>Cell: 256-619-7150</div>
      <div class="contact-gap"></div>
      <div>halvorsenconstruction@qrm.net</div>
      <div>halvorsenconstruction.com</div>
    </section>
  </article>
</main>
</body>
</html>
```